tallow-brook.com

We are a small dollar lending company that will revolutionize the industry. We will do this by being completely transparent, fee free, etc and an interest rate that normal people can afford to pay. Over 10X less than our competition. We only allow our members to pay bills " bills paid fast", within 72 hours. Payday loans typically charge from 390%-600% with a terrible payback structure. We charge 36%, period, with a payback structure over 12 months. Our site will be very simple and easy to use but elegant at the same time. We do not want the site to be too busy, less is more and easier. We will have; Home, The Story, Why tallowbrook.com, Are you eligible? Members, Clients. To become a member you have to be referred by a current client of tallowbrook.com. A lot of the busy stuff will be saved for the Members and Clients sections. The feel must be elegant, easy to use and very simple to understand. I am looking for the green, white and black combinations of colors, very similar to my logo that was designed by Fernquillo.

```html
<!DOCTYPE html>
<html lang="en">
<head>
<meta charset="utf-8">
<title>Tallow Brook — Fair Small Dollar Lending</title>
<link href="https://fonts.googleapis.com/css2?family=Open+Sans:wght@300;400;600;700&display=swap" rel="stylesheet">
<style>
:root{
  --green:#8dc63f;
  --green-dark:#7cb32f;
  --black:#000;
  --ink:#333;
  --text:#555;
  --grey-line:#d8d8d8;
  --panel:rgba(40,40,40,.92);
  --orange:#f0892b;
  --blue:#36a9ea;
  --white:#fff;
}
*{margin:0;padding:0;box-sizing:border-box}
html,body{width:722px;height:1200px;overflow:hidden;background:var(--white)}
body{font-family:"Open Sans",Arial,sans-serif;color:var(--text);position:relative}
.abs{position:absolute}

/* header */
.site-header{position:absolute;left:0;top:0;width:722px;height:54px;background:var(--green)}
.brand{position:absolute;left:80px;top:14px;display:flex;align-items:center;gap:6px;color:var(--white);font-size:14px;font-weight:400;letter-spacing:.5px}
.brand-dot{width:22px;height:22px;border-radius:50%;border:3px solid var(--white)}
.main-nav{position:absolute;left:279px;top:16px;display:flex;font-size:8px;text-transform:uppercase}
.main-nav a{color:var(--white);text-decoration:none;height:22px;line-height:22px;padding:0 9px;margin-right:0}
.main-nav a.active{background:var(--black);padding:0 11px;margin-right:0}

/* hero */
.hero{position:absolute;left:0;top:54px;width:722px;height:378px;
  background:linear-gradient(180deg,#cfe4f2 0%,#e9f2f4 40%,#b9cf86 70%,#6f8f2c 88%,#d24a1c 100%)}
.hero-dots{position:absolute;right:88px;top:24px;display:flex;gap:6px}
.hero-dots span{width:7px;height:7px;border-radius:50%;background:rgba(255,255,255,.7)}
.hero-dots span.on{background:var(--white);box-shadow:0 0 0 2px var(--green)}
.hero-panel{position:absolute;left:78px;top:132px;width:275px;height:116px;background:var(--panel);padding:25px 12px 0 12px;color:var(--white)}
.hero-panel h1{font-weight:400;font-size:20px;letter-spacing:.3px;line-height:1;padding-left:2px}
.hero-panel p{font-size:10px;margin-top:4px}
.btn{display:inline-block;background:var(--green);color:var(--white);text-decoration:none;text-transform:uppercase}
.hero-panel .btn{margin-top:12px;width:97px;height:26px;line-height:26px;text-align:center;font-size:9px}

/* intro */
.intro{position:absolute;left:80px;top:460px;width:559px;text-align:center}
.intro h2{font-weight:400;font-size:14px;color:#444;letter-spacing:.3px}
.intro p{font-size:7.6px;line-height:9.5px;margin-top:7px}
.rule{position:absolute;left:80px;width:559px;height:1px;background:var(--grey-line)}

/* flow */
.flow{position:absolute;left:120px;top:560px}
.role{position:absolute;font-size:10px;font-weight:600;color:var(--black);text-transform:uppercase;text-align:center;width:90px}

/* columns */
.col-title{position:absolute;font-weight:400;font-size:13px;color:#333;letter-spacing:.3px}
.video{position:absolute;left:79px;top:742px;width:257px;height:165px;
  background:linear-gradient(180deg,#3d6fb2 0%,#8ab2d8 45%,#9aa3a6 65%,#5c7448 100%)}
.caption{position:absolute;left:80px;top:917px;width:256px;font-size:7.6px;line-height:9.5px}
.how{position:absolute;left:358px;top:741px;width:281px}
.how p{font-size:7.6px;line-height:9.5px;text-align:justify}
.how ul{list-style:none;margin-top:10px}
.how li{font-size:7.6px;height:17.6px;padding-left:14px;position:relative}
.how li::before{content:"";position:absolute;left:0;top:3px;width:5px;height:5px;border:1.3px solid var(--green);border-radius:50%}
.apply{position:absolute;left:556px;top:917px;width:82px;height:26px;line-height:26px;text-align:center;font-size:10px;font-weight:600}

/* footer */
.site-footer{position:absolute;left:0;top:990px;width:722px;height:210px;background:var(--black);color:#bbb}
.f-title{position:absolute;color:var(--green);font-size:9px;font-weight:600;text-transform:uppercase;top:24px}
.f-list{position:absolute;top:37px;list-style:none;font-size:6.4px;line-height:8px;text-transform:uppercase}
.testimonial-photo{position:absolute;left:423px;top:39px;width:67px;height:65px;background:linear-gradient(180deg,#8a7560,#5b4a3d 60%,#3a2f2a)}
.quote{position:absolute;left:498px;top:40px;width:141px}
.quote h3{font-weight:400;font-size:10px;color:#999}
.quote p{font-size:7.3px;line-height:9px;color:#888;text-align:justify;margin-top:5px}
.author{position:absolute;left:424px;top:113px;font-size:7.3px;line-height:9px;color:#888}
.author b{color:#aaa;font-weight:600}
.subscribe{position:absolute;left:80px;top:139px;display:flex}
.subscribe input{width:142px;height:22px;border:0;padding:0 10px;font-family:inherit;font-size:7px;font-style:italic;color:#888}
.subscribe button{width:57px;height:22px;border:0;background:var(--green);color:var(--white);font-family:inherit;font-size:10px}
.social{position:absolute;left:541px;top:161px;display:flex;gap:8.5px;list-style:none}
.social li{width:18px;height:18px;border-radius:50%}
.copyright{position:absolute;right:83px;top:186px;font-size:6.2px;color:#aaa;text-transform:uppercase}
</style>
</head>
<body>

<header class="site-header">
  <div class="brand"><span class="brand-dot"></span><span>TALLOW BROOK</span></div>
  <nav class="main-nav">
    <a class="active" href="#">Home</a>
    <a href="#">The Story</a>
    <a href="#">Why tallowbrook.com</a>
    <a href="#">Are you eligible?</a>
    <a href="#">Members</a>
    <a href="#">Clients</a>
  </nav>
</header>

<section class="hero" role="img" aria-label="Photo of a happy family playing in a sunny poppy field with petals flying">
  <div class="hero-dots"><span class="on"></span><span></span><span></span><span></span></div>
  <div class="hero-panel">
    <h1>NEQUE PORRO QUISQUAM</h1>
    <p>In tune with the nature that extends wide range of</p>
    <a class="btn" href="#">Know More</a>
  </div>
</section>

<section class="intro">
  <h2>NEQUE PORRO QUISQUAM EST QUI DOLOREM</h2>
  <p>We are pioneering the first online microlending community to connect lenders and borrowers directly across international borders - overcoming previously insurmountable barriers of geography, wealth and circumstance.</p>
</section>
<div class="rule" style="top:537px"></div>

<svg class="flow" width="480" height="110" viewBox="0 0 480 110" aria-label="Lender and entrepreneur connected by direct funding and direct dialogue">
  <!-- lender icon -->
  <g fill="var(--orange)">
    <ellipse cx="42" cy="30" rx="11" ry="13"/>
    <path d="M17 72 Q17 46 42 44 Q67 46 67 72 Z"/>
  </g>
  <!-- entrepreneur icon -->
  <g fill="var(--blue)">
    <ellipse cx="427" cy="30" rx="11" ry="13"/>
    <path d="M402 72 Q402 46 427 44 Q452 46 452 72 Z"/>
  </g>
  <!-- arrow 1 -->
  <path fill="var(--green)" d="M98 32 L125 12 L125 22 L341 22 L341 12 L368 32 L341 52 L341 42 L125 42 L125 52 Z"/>
  <!-- arrow 2 -->
  <path fill="var(--green)" d="M98 77 L125 57 L125 67 L341 67 L341 57 L368 77 L341 97 L341 87 L125 87 L125 97 Z"/>
  <rect x="126" y="10" width="214" height="11" fill="#fff"/>
  <rect x="126" y="51" width="214" height="15" fill="#fff"/>
  <text x="233" y="18" text-anchor="middle" font-family="Open Sans, sans-serif" font-size="10" fill="#111">Direct Funding</text>
  <text x="233" y="36" text-anchor="middle" font-family="Open Sans, sans-serif" font-size="7.5" fill="#fff">Sed in tristique metus. Sed ac rutrum.</text>
  <text x="233" y="62" text-anchor="middle" font-family="Open Sans, sans-serif" font-size="10" fill="#111">Direct dialougeand updates</text>
  <text x="233" y="80" text-anchor="middle" font-family="Open Sans, sans-serif" font-size="7.5" fill="#fff">Proin iaculis tortor congue</text>
</svg>
<div class="role" style="left:117px;top:638px">Lender</div>
<div class="role" style="left:500px;top:638px;width:90px">Entrepreneur</div>

<div class="rule" style="top:690px"></div>

<h2 class="col-title" style="left:80px;top:711px">ABOUT TALLOW BROOK</h2>
<div class="video" role="img" aria-label="Video thumbnail of a modern glass office building under a blue sky">
  <svg width="257" height="165" viewBox="0 0 257 165" aria-hidden="true">
    <circle cx="128" cy="82" r="20" fill="rgba(255,255,255,.2)" stroke="#fff" stroke-width="2.5"/>
    <path d="M122 71 L138 82 L122 93 Z" fill="#fff"/>
  </svg>
</div>
<p class="caption">Class aptent taciti sociosqu ad litora torquent per conubia nostra, per inceptos himenaeos. Suspendisse ut quam quis dolor ullamcorper condimentum a nec felis.</p>

<h2 class="col-title" style="left:357px;top:711px">HOW IT WORKS ?</h2>
<section class="how">
  <p>Sed in tristique metus. Sed ac rutrum neque. Proin iaculis tortor congue, facilisis elit ac, pharetra odio. Maecenas molestie neque sollicitudin mattis accumsan. Sed vulputate augue et odio luctus laoreet. Etiam vulputate mi et libero imperdiet suscipit. Cras eu velit sed massa rhoncus porttitor non ac massa. Vestibulum pellentesque libero quis ornare blandit. Nam fermentum felis eu augue eleifend vehicula.</p>
  <ul>
    <li>Proin iaculis tortor congue, facilisis elit ac, pharetra odio.</li>
    <li>Maecenas molestie neque sollicitudin mattis accumsan.</li>
    <li>Sed vulputate augue et odio luctus laoreet.</li>
    <li>Etiam vulputate mi et libero imperdiet suscipit.</li>
    <li>Cras eu velit sed massa rhoncus porttitor non ac massa.</li>
    <li>Vestibulum pellentesque libero quis ornare blandit.</li>
  </ul>
</section>
<a class="btn apply" href="#">Apply Now</a>

<footer class="site-footer">
  <h4 class="f-title" style="left:80px">Menu</h4>
  <ul class="f-list" style="left:80px">
    <li>Home</li><li>The Story</li><li>Why tallowbrook.com</li><li>Are you eligible?</li><li>Members</li><li>Clients</li>
  </ul>
  <h4 class="f-title" style="left:165px">Company</h4>
  <ul class="f-list" style="left:165px">
    <li>Team</li><li>Privacy Policy</li><li>Terms of Service</li><li>Careers</li><li>Brand Assets</li>
  </ul>
  <h4 class="f-title" style="left:270px">Contact Us</h4>
  <ul class="f-list" style="left:270px">
    <li>Sample Address,</li><li>Marlow QLD 4102</li><li>Unites States</li><li>1800 5 27710</li><li>(07) 3190 4428</li>
  </ul>

  <h4 class="f-title" style="left:423px">Client Testimonials</h4>
  <div class="testimonial-photo" role="img" aria-label="Portrait photo of the client"></div>
  <div class="quote">
    <h3>One word IMPRESSIVE!!!</h3>
    <p>Class aptent taciti sociosqu ad litora torquent per conubia nostra, per inceptos himenaeos. Suspendisse ut quam quis felis.</p>
  </div>
  <div class="author"><b>Ravi Lenholm</b><br>CTO, Brightfold</div>

  <h4 class="f-title" style="left:80px;top:118px;font-weight:400;font-size:10px">Subscribe Newsletter</h4>
  <form class="subscribe">
    <input type="text" placeholder="enter your mail address">
    <button type="button">submit</button>
  </form>

  <ul class="social">
    <li style="background:#1da1f2" aria-label="Social profile 1"></li>
    <li style="background:#3b5998" aria-label="Social profile 2"></li>
    <li style="background:#dd4b39" aria-label="Social profile 3"></li>
    <li style="background:#0077b5" aria-label="Social profile 4"></li>
  </ul>
  <p class="copyright">Copyright 2007 © Tallow Brook | &nbsp;All rights reserved. Privacy Policy</p>
</footer>

</body>
</html>
```